Business card for medical clinic

I need an upmarket, modern medical/health business card for my clinic

Contact Information for Business Card

name, address, email, qr code

```html
<!DOCTYPE html>
<html lang="en">
<head>
<meta charset="utf-8">
<title>Corvale Health Partners – Business Card</title>
<link href="https://fonts.googleapis.com/css2?family=Gelasio:wght@400;700&display=swap" rel="stylesheet">
<style>
  :root {
    --canvas: #e2e3e6;
    --navy: #1c3352;
    --navy-deep: #172a45;
    --blue: #1a8fd0;
    --blue-bright: #1ea0e0;
    --white: #ffffff;
    --ink: #2a2f36;
    --shadow: rgba(20, 30, 50, 0.18);
  }
  * { box-sizing: border-box; margin: 0; padding: 0; }
  html, body { width: 1200px; height: 800px; overflow: hidden; }
  body {
    background: var(--canvas);
    font-family: "Gelasio", Georgia, serif;
    display: flex;
    align-items: center;
    justify-content: center;
    gap: 40px;
  }
  .card {
    width: 525px;
    height: 300px;
    position: relative;
    overflow: hidden;
    box-shadow: 0 10px 30px var(--shadow);
  }

  /* Front */
  .card-front {
    background: radial-gradient(ellipse at 28% 30%, var(--blue-bright) 0%, #1a6ea6 38%, var(--navy) 78%, var(--navy-deep) 100%);
    display: flex;
    align-items: center;
    padding-left: 60px;
  }
  .brand {
    display: flex;
    align-items: center;
    gap: 14px;
  }
  .brand-dot {
    width: 34px;
    height: 34px;
    border-radius: 50%;
    flex: none;
  }
  .brand-name {
    font-weight: 400;
    letter-spacing: 2px;
    text-transform: uppercase;
    line-height: 1.2;
  }
  .card-front .brand { margin-top: -40px; }
  .card-front .brand-dot { border: 3px solid var(--white); }
  .card-front .brand-name { color: var(--white); font-size: 25px; }

  /* Back */
  .card-back { background: var(--white); }
  .contact {
    position: absolute;
    left: 40px;
    top: 40px;
  }
  .person-name {
    font-weight: 700;
    font-size: 19px;
    letter-spacing: 0.5px;
    color: var(--blue);
    text-transform: uppercase;
  }
  .person-role {
    font-size: 15px;
    color: var(--ink);
    margin-bottom: 16px;
  }
  .contact-list { list-style: none; }
  .contact-list li {
    display: flex;
    align-items: center;
    gap: 8px;
    font-size: 15px;
    color: var(--ink);
    line-height: 1.6;
  }
  .contact-list svg { width: 13px; height: 13px; flex: none; }
  .address-band {
    position: absolute;
    left: 0;
    bottom: 62px;
    width: 300px;
    height: 34px;
    background: linear-gradient(90deg, var(--navy) 0%, var(--navy) 25%, var(--blue) 100%);
    color: var(--white);
    font-size: 15px;
    display: flex;
    align-items: center;
    padding-left: 22px;
  }
  .card-back .brand {
    position: absolute;
    right: 32px;
    top: 110px;
    gap: 10px;
  }
  .card-back .brand-dot { border: 3px solid var(--blue); width: 30px; height: 30px; }
  .card-back .brand-name { color: var(--navy); font-size: 19px; }
</style>
</head>
<body>

  <section class="card card-front" aria-label="Card front">
    <div class="brand">
      <span class="brand-dot"></span>
      <span class="brand-name">Corvale Health<br>Partners</span>
    </div>
  </section>

  <section class="card card-back" aria-label="Card back">
    <div class="contact">
      <p class="person-name">Elena Marsh</p>
      <p class="person-role">Director</p>
      <ul class="contact-list">
        <li>
          <svg viewBox="0 0 16 16" aria-hidden="true"><path fill="#1a8fd0" d="M3.6 1.5l2.3 2.6-1.3 1.7c.9 2 2.4 3.6 4.6 4.7l1.6-1.3 2.7 2.2-1.2 2.4C7.2 13.5 2.5 8.9 1.8 3.2z"/></svg>
          410-555-0182
        </li>
        <li>
          <svg viewBox="0 0 16 16" aria-hidden="true"><rect x="1" y="3" width="14" height="10" fill="none" stroke="#1a8fd0" stroke-width="1.6"/><path d="M1 3l7 6 7-6" fill="none" stroke="#1a8fd0" stroke-width="1.6"/></svg>
          info@corvalehealth.com
        </li>
        <li>
          <svg viewBox="0 0 16 16" aria-hidden="true"><g fill="none" stroke="#1a8fd0" stroke-width="1.3"><circle cx="8" cy="8" r="6.5"/><ellipse cx="8" cy="8" rx="3" ry="6.5"/><path d="M1.5 8h13M2.5 4.8h11M2.5 11.2h11"/></g></svg>
          www.corvalehealth.com
        </li>
      </ul>
    </div>
    <div class="address-band">00 dummy city, dummy place 0000</div>
    <div class="brand">
      <span class="brand-dot"></span>
      <span class="brand-name">Corvale Health<br>Partners</span>
    </div>
  </section>

</body>
</html>
```